Brookvale Building Company - advertisement poster

I am looking to print some canvas signs to advertise my general contracting company, Brookvale Building Company. The sign will measure 6' long x 3' high so the size should match that ratio. I already have a logo icon, which is the Letter 'B' and some trees that I would like to incorporate, see attached. I would also like the to have the following information listed:
1) phone number: 831-555-0172
2) email: brookvalebuildingcompany@mailnest.example
3) website: brookvalebuildingcompany.example
4) Lic#4826130
5) I want to use this text: "BUILD WITH THE B-CREW!"

The ad should be relatively simple and clean. Black and Green are my company colors. I am open to creative ideas!

Target Market(s)

People looking to renovate their homes

Industry/Entity Type

Construction

Colors
59FF00
82FF00
B8FF75
E3FFCB
F4FFEA

Requirements
Must have
• Must have my company logo
Should not have
• No photos or complex graphics

```html
<!DOCTYPE html>
<html lang="en">
<head>
<meta charset="utf-8">
<title>Brookvale Building Company – Sign</title>
<link href="https://fonts.googleapis.com/css2?family=Michroma&family=Saira+Stencil+One&family=Inter:wght@400;700&display=swap" rel="stylesheet">
<style>
  :root {
    --page: #e9ebec;
    --black: #000000;
    --green: #6fb746;
    --white: #ffffff;
    --ink: #0b0b0b;
  }
  html, body {
    margin: 0;
    width: 1200px;
    height: 800px;
    overflow: hidden;
    background: var(--page);
  }
  .sign {
    position: absolute;
    left: 40px;
    top: 157px;
    width: 1120px;
    height: 486px;
    background: var(--black);
    overflow: hidden;
  }
  .sign__diagonal {
    position: absolute;
    inset: 0;
    width: 100%;
    height: 100%;
  }
  .brand {
    position: absolute;
    left: 94px;
    top: 88px;
    width: 320px;
    text-align: center;
    font-family: "Michroma", sans-serif;
    color: var(--white);
  }
  .brand__mark {
    width: 58px;
    height: 58px;
    margin: 0 auto 14px;
    background: var(--green);
  }
  .brand__name {
    margin: 0;
    font-weight: 400;
    line-height: 1.1;
  }
  .brand__name-main {
    display: block;
    font-size: 31px;
    letter-spacing: 0.5px;
  }
  .brand__name-sub {
    display: block;
    margin-top: 6px;
    font-size: 14.5px;
    letter-spacing: 4.6px;
  }
  .estd {
    position: absolute;
    top: 139px;
    font-family: "Michroma", sans-serif;
    font-size: 10px;
    letter-spacing: 2.5px;
    color: var(--white);
    padding: 4px 0;
    border-top: 1px solid var(--green);
    border-bottom: 1px solid var(--green);
  }
  .estd--label { left: 114px; }
  .estd--year { left: 345px; }
  .license {
    position: absolute;
    left: 876px;
    top: 98px;
    margin: 0;
    font-family: "Inter", sans-serif;
    font-size: 19px;
    color: var(--ink);
  }
  .headline {
    position: absolute;
    left: 512px;
    top: 206px;
    margin: 0;
    font-family: "Saira Stencil One", sans-serif;
    font-weight: 400;
    color: var(--ink);
    line-height: 1;
  }
  .headline__lead {
    display: block;
    margin-left: 117px;
    font-size: 43px;
    letter-spacing: 2px;
  }
  .headline__crew {
    display: block;
    margin-top: -2px;
    font-size: 96px;
    letter-spacing: 6px;
  }
  .contact {
    position: absolute;
    left: 578px;
    top: 346px;
    margin: 0;
    padding: 0;
    list-style: none;
    font-family: "Inter", sans-serif;
    color: var(--ink);
  }
  .contact__item {
    display: flex;
    align-items: center;
    height: 37px;
  }
  .contact__icon {
    width: 22px;
    height: 22px;
    margin-right: 43px;
    flex: none;
  }
  .contact__text { font-size: 20px; }
  .contact__item--phone .contact__text {
    font-size: 31px;
    font-weight: 700;
    letter-spacing: 0.5px;
  }
</style>
</head>
<body>
<main class="sign">
  <svg class="sign__diagonal" viewBox="0 0 1120 486" preserveAspectRatio="none" aria-hidden="true">
    <polygon points="715,4 1116,4 1116,486 171,486" fill="var(--green)"/>
  </svg>

  <span class="estd estd--label">ESTD</span>
  <span class="estd estd--year">2020</span>
  <div class="brand">
    <div class="brand__mark" aria-hidden="true"></div>
    <h1 class="brand__name">
      <span class="brand__name-main">BROOKVALE</span>
      <span class="brand__name-sub">BUILDING COMPANY</span>
    </h1>
  </div>

  <p class="license">Lic#4826130Z</p>

  <h2 class="headline">
    <span class="headline__lead">BUILD WITH THE</span>
    <span class="headline__crew">B-CREW</span>
  </h2>

  <ul class="contact">
    <li class="contact__item contact__item--phone">
      <svg class="contact__icon" viewBox="0 0 24 24" aria-hidden="true">
        <circle cx="12" cy="12" r="12" fill="var(--ink)"/>
        <rect x="8.5" y="5" width="7" height="14" rx="1.5" fill="none" stroke="var(--green)" stroke-width="1.6"/>
      </svg>
      <span class="contact__text">831-555-0172</span>
    </li>
    <li class="contact__item">
      <svg class="contact__icon" viewBox="0 0 24 24" aria-hidden="true">
        <circle cx="12" cy="12" r="12" fill="var(--ink)"/>
        <rect x="5.5" y="7.5" width="13" height="9" rx="1" fill="none" stroke="var(--green)" stroke-width="1.6"/>
        <polyline points="5.5,8 12,13 18.5,8" fill="none" stroke="var(--green)" stroke-width="1.6"/>
      </svg>
      <span class="contact__text">brookvalebuildingcompany@mailnest.example</span>
    </li>
    <li class="contact__item">
      <svg class="contact__icon" viewBox="0 0 24 24" aria-hidden="true">
        <circle cx="12" cy="12" r="12" fill="var(--ink)"/>
        <circle cx="12" cy="12" r="7" fill="none" stroke="var(--green)" stroke-width="1.5"/>
        <ellipse cx="12" cy="12" rx="3" ry="7" fill="none" stroke="var(--green)" stroke-width="1.5"/>
        <line x1="5" y1="12" x2="19" y2="12" stroke="var(--green)" stroke-width="1.5"/>
      </svg>
      <span class="contact__text">brookvalebuildingcompany.example</span>
    </li>
  </ul>
</main>
</body>
</html>
```